Growing the Ironclad Young Contender:
A Family Playbook for Nurturing Bold, Grounded, and Resilient Daughters at Games and Beyond.
📘 Book Cover Design Brief – “Growing the Ironclad Young Contender”

Project Title:
Design a bold, inspiring book cover for a best-selling book titled:
Growing the Ironclad Young Contender
Subtitle: A Family Playbook for Nurturing Bold, Grounded, and Resilient Daughters at Games and Beyond

🎯 Audience:

Parents of female athletes ages 14–20 who want their daughters to build confidence, strength, resilience, and long-term success both in sports and in life.

This book should feel encouraging, empowering, and credible — NOT cheesy, childish, or overly academic.

📕 Design Tone & Style:

Powerful and professional — should feel like a best-selling book from a leading performance or parenting expert

Emotionally compelling — conveys hope, resilience, strength, and possibility

Visually modern and clean — avoid anything overly busy, cliché, or childish

Heroic/aspirational tone — think transformation, leadership, strong positioning

💡 Visual Direction / Ideas (Use as Inspiration, Not Limitation):

Strong, confident teenage female athlete imagery — adaptable beyond one specific sport

Symbolic visuals — e.g. athlete standing strong, on a starting line, looking bold into the future, silhouette, or power stance

Bold typography that feels clean and modern (e.g., Proxima Nova, Montserrat, Gotham, Bebas Neue, etc.)

A title that stands out clearly when viewed as a thumbnail on Brindlemart

Color tones: Empowering, modern, and strong: think deep blues, greens, purples, or golds — avoid playful pastels or overly girly themes

Potential imagery: textured backgrounds, motion, bravery, development, strength, growth, sport/action overlays

🔥 What the Cover MUST Communicate:

✅ This is for parents who want strong, confident female athletes
✅ It’s a guidebook for personal development AND sports performance
✅ It’s about creating “IRONCLAD” confidence — physically, mentally and emotionally
✅ The message is: You can help your daughter become her strongest, most confident self

📚 Back-of-Book Summary (for context):

"Growing the Ironclad Young Contender" is a parent's blueprint to building girls who are strong in body, confident in mind, and ready to lead on and off the field. Through simple strategies around strength training, mindset, nutrition, and character development, this book gives parents the tools to help their daughters stay injury-resistant, break through mental barriers, and unlock their full potential — in sports and in life.

✅ Deliverables:

Full cover design (front, back, spine) for paperback
High-resolution files (print-ready)
Source files (PSD, AI, etc.)
3D mockup versions of the book (standing, flat, stack)

Target Market(s)

Industry/Entity Type

Fitness

Font styles to use
Sans Serif

Colors
FFF300
FFF600
FEFA6F
FFFEC7
FFFEE8

Requirements
Must have
• Bold Font
Should not have
• I don't want an image of a female athlete. I want this to be font based.

```html
<!DOCTYPE html>
<html lang="en">
<head>
<meta charset="utf-8">
<title>Growing the Ironclad Young Contender – Full Cover</title>
<link rel="stylesheet" href="https://fonts.googleapis.com/css2?family=Bebas+Neue&family=League+Gothic&family=Arimo:ital,wght@1,700&display=swap">
<style>
  :root {
    --purple-deep: #2a0848;
    --purple-mid: #4a1775;
    --purple-glow: #9a68c8;
    --streak: rgba(255, 255, 255, 0.12);
    --white: #ffffff;
    --portrait-dark: #1a1a1a;
    --portrait-light: #3a3a3a;
    --figure-main: #8a4fc4;
    --figure-accent: #e9a679;
  }
  * { margin: 0; padding: 0; box-sizing: border-box; }
  html, body { width: 1200px; height: 866px; overflow: hidden; background: var(--purple-deep); }
  .cover {
    position: relative;
    width: 1200px;
    height: 866px;
    overflow: hidden;
    background:
      radial-gradient(ellipse 260px 300px at 960px 450px, rgba(180, 130, 220, 0.55), transparent 70%),
      linear-gradient(135deg, var(--purple-mid) 0%, var(--purple-deep) 35%, #3b0f62 55%, var(--purple-deep) 100%);
  }
  .streaks { position: absolute; inset: 0; pointer-events: none; }
  .back-blurb {
    position: absolute;
    left: 105px; top: 152px; width: 377px;
    font-family: "Bebas Neue", sans-serif;
    font-size: 16.6px;
    line-height: 23.4px;
    color: var(--white);
    text-align: justify;
    text-align-last: left;
  }
  .author-portrait {
    position: absolute;
    left: 226px; top: 343px; width: 136px; height: 160px;
    border: 2px solid var(--white);
    background: radial-gradient(ellipse at 50% 40%, var(--portrait-light), var(--portrait-dark) 75%);
  }
  .author-bio {
    position: absolute;
    left: 110px; top: 519px; width: 376px;
    font-family: "Bebas Neue", sans-serif;
    font-size: 13.6px;
    line-height: 17.6px;
    color: var(--white);
    text-align: justify;
    text-align-last: left;
  }
  .barcode-area {
    position: absolute;
    left: 323px; top: 667px; width: 198px; height: 100px;
    background: var(--white);
  }
  .spine, .front-title, .author-name { position: absolute; overflow: visible; }
  .spine { left: 574px; top: 140px; }
  .front-title { left: 690px; top: 70px; }
  .title-text { font-family: "League Gothic", sans-serif; fill: var(--white); filter: drop-shadow(2px 2px 2px rgba(0,0,0,0.45)); }
  .athlete-figure {
    position: absolute;
    left: 915px; top: 329px; width: 212px; height: 237px;
    background: radial-gradient(ellipse 60% 70% at 55% 55%, var(--figure-main), rgba(138, 79, 196, 0) 75%);
  }
  .subtitle {
    position: absolute;
    left: 700px; top: 584px; width: 418px;
    font-family: "Arimo", sans-serif;
    font-style: italic; font-weight: 700;
    font-size: 19.5px; line-height: 25.5px;
    color: var(--white);
    text-align: center;
    text-transform: uppercase;
    text-shadow: 1px 1px 2px rgba(0,0,0,0.35);
  }
  .author-name { left: 748px; top: 698px; }
</style>
</head>
<body>
<main class="cover">
  <svg class="streaks" width="1200" height="866" viewBox="0 0 1200 866" aria-hidden="true">
    <polygon points="0,40 90,0 130,0 0,120" fill="var(--streak)"/>
    <polygon points="0,330 330,0 360,0 0,360" fill="rgba(255,255,255,0.06)"/>
    <polygon points="0,866 0,790 120,866" fill="var(--streak)"/>
    <polygon points="1200,20 1200,90 1090,0 1140,0" fill="rgba(255,255,255,0.09)"/>
    <polygon points="1200,620 1200,700 1030,866 960,866" fill="rgba(255,255,255,0.08)"/>
    <polygon points="600,866 820,640 860,640 650,866" fill="rgba(255,255,255,0.05)"/>
  </svg>

  <p class="back-blurb">"Growing the Ironclad Young Contender" is a parent's blueprint to building girls who are strong in body, confident in mind, and ready to lead on and off the field. Through simple strategies around strength training, mindset, nutrition, and character development, this book gives parents the tools to help their daughters stay injury-resistant, break through mental barriers, and unlock their full potential — in sports and in life.</p>

  <div class="author-portrait" role="img" aria-label="Portrait photo of the author, smiling, in a dark training shirt"></div>

  <p class="author-bio">Jordan has 15 years experience, specializing in personal training and sport performance. He focuses his training on creating programs that improve performance and reduce the risk of injury. Jordan has worked with clients from 8 – 73. He is a 2 time Brindlemart best-selling author with Rise Every Day and Peak Fuel for Young Competitors. Jordan commits his life to coaching each client to be great. Stride Fitness was born out of his passion to make each person who walks in the door the very best version of themselves.</p>

  <div class="barcode-area" aria-hidden="true"></div>

  <svg class="spine" width="50" height="540" viewBox="0 0 50 540" aria-label="Spine: Growing the Ironclad Young Contender, Jordan Kessler">
    <g transform="translate(14,5) rotate(90)">
      <text class="title-text" x="0" y="0" font-family="Bebas Neue, sans-serif" font-size="27" textLength="335" lengthAdjust="spacingAndGlyphs">GROWING THE IRONCLAD YOUNG CONTENDER</text>
      <text class="title-text" x="388" y="0" font-family="Bebas Neue, sans-serif" font-size="29" textLength="138" lengthAdjust="spacingAndGlyphs">JORDAN KESSLER</text>
    </g>
  </svg>

  <svg class="front-title" width="450" height="490" viewBox="0 0 450 490" role="heading" aria-level="1" aria-label="Growing the Ironclad Young Contender">
    <text class="title-text" x="96" y="114" font-size="140" textLength="192" lengthAdjust="spacingAndGlyphs">GROWING</text>
    <text class="title-text" x="296" y="114" font-size="60" textLength="58" lengthAdjust="spacingAndGlyphs">THE</text>
    <text class="title-text" x="8" y="254" font-size="178" textLength="430" lengthAdjust="spacingAndGlyphs">IRONCLAD</text>
    <text class="title-text" x="8" y="364" font-size="138" textLength="210" lengthAdjust="spacingAndGlyphs">YOUNG</text>
    <text class="title-text" x="8" y="476" font-size="138" textLength="218" lengthAdjust="spacingAndGlyphs">CONTENDER</text>
  </svg>

  <div class="athlete-figure" role="img" aria-label="Illustration of a young female athlete in a lunging stretch with arms raised"></div>

  <p class="subtitle">A Family Playbook for Nurturing Bold, Grounded, and Resilient Daughters at Games and Beyond</p>

  <svg class="author-name" width="330" height="70" viewBox="0 0 330 70" aria-label="Jordan Kessler">
    <text class="title-text" x="2" y="64" font-family="Bebas Neue, sans-serif" font-size="78" textLength="316" lengthAdjust="spacing">JORDAN KESSLER</text>
  </svg>
</main>
</body>
</html>
```